Boutique custom software development company needs new business card

Our nearly 20 year old custom software development company would like to better include the fact that we are now providing Bitcoin services. These new services are B2B include education (how to acquire and securely hold Bitcoin) and integrating Bitcoin payments into existing ecommerce sites or other existing systems. Please keep the card clean and simple. Attached is our current design and some other files. vextorial.com

Target Market(s)

businesses owners interested in long term relationship

Industry/Entity Type

Custom software development and Bitcoin

Contact Information for Business Card

Dale Parker, dale@vextorial.com, vextorial.com, (888) 555-VXTRL

Font styles to use
Other font styles liked:
• monospace

Requirements
Must have
• double-sided
Nice to have
• clean and simple
Should not have
• physical address

```html
<!DOCTYPE html>
<html lang="en">
<head>
<meta charset="utf-8">
<title>Vextorial Business Card</title>
<link rel="stylesheet" href="https://fonts.googleapis.com/css2?family=Courier+Prime:wght@400;700&family=Lato:wght@300;400;900&family=Source+Sans+3:wght@400&display=swap">
<style>
  :root {
    --backdrop: #5e5d5e;
    --paper: #ffffff;
    --brand-blue: #3e72b7;
    --brand-orange: #f07b23;
    --ink-light: #ffffff;
  }
  * { margin: 0; padding: 0; box-sizing: border-box; }
  html, body {
    width: 1200px; height: 1200px; overflow: hidden;
    background: var(--backdrop);
  }
  .card {
    position: absolute; left: 250px; width: 700px; height: 400px;
    overflow: hidden;
    box-shadow: 0 2px 6px rgba(0,0,0,0.35);
  }
  .card--front { top: 170px; background: var(--paper); }
  .card--back { top: 631px; background: var(--brand-blue); }

  .brand {
    position: absolute; left: 0; right: 0; top: 88px; text-align: center;
  }
  .brand__name {
    font-family: "Lato", sans-serif; font-weight: 900;
    font-size: 66px; line-height: 66px; letter-spacing: 1px;
    color: var(--brand-blue);
  }
  .brand__tagline {
    margin-top: 8px;
    font-family: "Lato", sans-serif; font-weight: 400;
    font-size: 22px; letter-spacing: -0.9px;
    color: var(--brand-blue);
  }

  .contact-band {
    position: absolute; left: 0; top: 268px; width: 347px; height: 132px;
    background: var(--brand-blue);
  }
  .contact-list {
    list-style: none; position: absolute; left: 46px; top: 27px;
    font-family: "Courier Prime", monospace; font-size: 17px;
    color: var(--ink-light);
  }
  .contact-list li { display: flex; align-items: center; height: 24.5px; }
  .contact-list svg { width: 14px; height: 14px; margin-right: 11px; flex: none; }

  .name-band {
    position: absolute; left: 351px; top: 268px; width: 349px; height: 132px;
    background: var(--brand-orange);
    color: var(--ink-light); text-align: right;
  }
  .person {
    position: absolute; right: 47px; top: 35px;
    font-family: "Courier Prime", monospace;
  }
  .person__name { font-weight: 700; font-size: 34px; line-height: 34px; letter-spacing: 0.5px; }
  .person__title { font-size: 18px; line-height: 22px; margin-top: 2px; }

  .back-corner { position: absolute; left: 0; top: 0; }
  .back-brand {
    position: absolute; left: 40px; top: 150px;
    font-family: "Lato", sans-serif; font-weight: 900;
    font-size: 58px; color: var(--ink-light); letter-spacing: 1px;
  }
  .services {
    list-style: none; position: absolute; right: 46px; top: 253px;
    font-family: "Source Sans 3", sans-serif; font-size: 18.5px;
    color: var(--ink-light); text-align: right;
  }
  .services li { height: 26.7px; display: flex; justify-content: flex-end; align-items: center; }
  .services li::after {
    content: ""; width: 8px; height: 8px; margin-left: 12px;
    background: var(--ink-light);
  }
</style>
</head>
<body>

<section class="card card--front">
  <div class="brand">
    <div class="brand__name">VEXTORIAL</div>
    <div class="brand__tagline">developer of custom applications</div>
  </div>

  <div class="contact-band">
    <ul class="contact-list">
      <li>
        <svg viewBox="0 0 16 16" aria-hidden="true"><path fill="#fff" d="M3.5 1.5l2.5 0 1 3.5-1.7 1.2a9 9 0 0 0 4.5 4.5L11 9l3.5 1v2.5c0 1-1 2-2 2C6.5 14.5 1.5 9.5 1.5 3.5c0-1 1-2 2-2z"/></svg>
        (888) 555-VXTRL
      </li>
      <li>
        <svg viewBox="0 0 16 16" aria-hidden="true"><rect x="1" y="3.5" width="14" height="9" fill="#fff"/><path d="M1.5 4l6.5 5 6.5-5" fill="none" stroke="#3e72b7" stroke-width="1.3"/></svg>
        dale@vextorial.com
      </li>
      <li>
        <svg viewBox="0 0 16 16" aria-hidden="true"><circle cx="8" cy="8" r="6.5" fill="none" stroke="#fff" stroke-width="1.6"/><ellipse cx="8" cy="8" rx="2.8" ry="6.5" fill="none" stroke="#fff" stroke-width="1.2"/><path d="M1.5 8h13" stroke="#fff" stroke-width="1.2"/></svg>
        vextorial.com
      </li>
    </ul>
  </div>

  <div class="name-band">
    <div class="person">
      <div class="person__name">DALE PARKER</div>
      <div class="person__title">Founding Partner</div>
    </div>
  </div>
</section>

<section class="card card--back">
  <svg class="back-corner" width="700" height="400" viewBox="0 0 700 400" aria-hidden="true">
    <polygon points="0,291 48,263 127,400 0,400" fill="var(--brand-orange)"/>
  </svg>
  <div class="back-brand">VEXTORIAL</div>
  <ul class="services">
    <li>Web &amp; Native Applications</li>
    <li>Digital Process Automation</li>
    <li>Cloud-Based Portals</li>
    <li>Bitcoin Consulting</li>
  </ul>
</section>

</body>
</html>
```